Birch Hauling Business Card Design Project

We need a new company business card. We provide professional timber harvesting (logging) and forest management services. I'm open to any creative design. Most company caps and shirts are navy blue and Light grey. Logo does not necessarily have to contain those colors. Logo containing picture of logging equipment, log truck, trees, or logs are acceptable. Be creative. Final logo should communicate our company's pride and professionalism in the East Texas Timber Industry.
Updates

Target Market(s)

Timber owners, sawmills, and forestry professionals

Industry/Entity Type

Business

Requirements
Must have
• Must have Contact Info.
Phone: 936-402-5917
address: PO Box 4830
Oak Bend, Tx 77014
www.jmbirchhauling.example
jmbirchhauling@mailbox.example
Owner: Jared Marsh

Or design must leave room for this info.

```html
<!DOCTYPE html>
<html lang="en">
<head>
<meta charset="utf-8">
<title>Birch Hauling Business Card</title>
<link rel="stylesheet" href="https://fonts.googleapis.com/css2?family=Lato:wght@400;700;900&display=swap">
<style>
  :root {
    --backdrop: #e8e8ec;
    --brand-blue: #3f3d91;
    --brand-navy: #26246f;
    --card-white: #ffffff;
    --text-grey: #767676;
    --rule-grey: #8a8a8a;
  }
  * { margin: 0; padding: 0; box-sizing: border-box; }
  html, body { width: 1200px; height: 960px; overflow: hidden; }
  body {
    background: var(--backdrop);
    font-family: "Lato", Arial, sans-serif;
    position: relative;
  }
  .card {
    position: absolute;
    left: 270px;
    width: 645px;
    height: 367px;
    box-shadow: 0 4px 10px rgba(0,0,0,0.25);
  }
  .card--front { top: 84px; background: var(--brand-blue); }
  .card--back { top: 508px; background: var(--card-white); }

  .front-mark {
    position: absolute;
    left: 0; right: 0; top: 126px;
    text-align: center;
    color: var(--card-white);
    font-weight: 900;
    font-size: 112px;
    line-height: 1;
    letter-spacing: 6px;
  }
  .front-url {
    position: absolute;
    left: 0; right: 0; top: 319px;
    text-align: center;
    color: var(--card-white);
    font-size: 14px;
    letter-spacing: 1.2px;
  }

  .brand-lockup {
    position: absolute;
    left: 63px; top: 162px;
    display: flex;
    align-items: center;
  }
  .brand-mark {
    color: var(--brand-blue);
    font-weight: 900;
    font-size: 42px;
    line-height: 1;
    letter-spacing: 4px;
    width: 99px;
    text-align: center;
  }
  .brand-rule {
    width: 2px; height: 36px;
    background: var(--rule-grey);
    margin: 0 11px 0 12px;
  }
  .brand-name { color: var(--text-grey); font-weight: 700; font-size: 15px; line-height: 19px; }
  .brand-slogan { color: var(--text-grey); font-size: 15px; line-height: 19px; }

  .contact {
    position: absolute;
    left: 362px; top: 94px;
    color: var(--text-grey);
    font-size: 15px;
  }
  .contact__name { color: var(--brand-navy); font-weight: 700; font-size: 20px; line-height: 22px; }
  .contact__role { line-height: 18px; }
  .contact__address { margin-top: 22px; line-height: 18.5px; }
  .contact__list { list-style: none; margin-top: 21px; }
  .contact__list li { display: flex; align-items: center; line-height: 18.5px; }
  .contact__list svg { width: 15px; height: 13px; margin-right: 11px; fill: var(--brand-navy); }
</style>
</head>
<body>
  <section class="card card--front">
    <div class="front-mark">JM</div>
    <div class="front-url">www.jmbirchhauling.example</div>
  </section>

  <section class="card card--back">
    <div class="brand-lockup">
      <div class="brand-mark">JM</div>
      <div class="brand-rule"></div>
      <div>
        <div class="brand-name">Company Name</div>
        <div class="brand-slogan">Your Slogan</div>
      </div>
    </div>

    <div class="contact">
      <div class="contact__name">Jared Marsh</div>
      <div class="contact__role">Owner</div>
      <div class="contact__address">PO Box 4830<br>Oak Bend, Tx 77014</div>
      <ul class="contact__list">
        <li>
          <svg viewBox="0 0 15 13" aria-hidden="true"><path d="M1 4C1 2 3 1 7.5 1S14 2 14 4v1h-3V3.5H4V5H1z"/><path d="M3 6h9l2 6H1z"/></svg>
          936-402-5917
        </li>
        <li>
          <svg viewBox="0 0 15 13" aria-hidden="true"><path d="M0 1h15v11H0z M1.5 2.5v.3L7.5 7l6-4.2v-.3z M1.5 4.6v6h12v-6L7.5 8.8z" fill-rule="evenodd"/></svg>
          jmbirchhauling@mailbox.example
        </li>
        <li>
          <svg viewBox="0 0 15 13" aria-hidden="true"><path d="M0 0h15v10H0z M1.5 1.5v7h12v-7z" fill-rule="evenodd"/><path d="M5 11h5v1.5H5z"/></svg>
          www.jmbirchhauling.example
        </li>
      </ul>
    </div>
  </section>
</body>
</html>
```